Business card for law firm

Need business card for new law firm. Think confident, authoritative, conservative, but not stuffy or old-fashioned.

Contact Information for Business Card

Content for card - logo (uploaded), plus the following:

Paul Whitcombe (larger font)
Managing Partner (larger font, but not as large as name)
Level 9, 7 Ferris Lane
Sydney NSW 2000
Main Tel 02 9364 2710
Direct Tel 02 8472 3159
Email paul@qvlegal.com.au
www.qvlegal.com.au

Letterhead design should include logo plus:
Level 9, 7 Ferris Lane
Sydney NSW 2000
Tel 02 8472 3159
www.qvlegal.com.au

```html
<!DOCTYPE html>
<html lang="en">
<head>
<meta charset="utf-8">
<title>Quayvale Legal — Business Card</title>
<link href="https://fonts.googleapis.com/css2?family=Cinzel:wght@600&family=Montserrat:wght@400;500&display=swap" rel="stylesheet">
<style>
  :root {
    --backdrop: #1c1c1e;
    --card-navy: #222c6c;
    --card-navy-deep: #1d2660;
    --ink-white: #ffffff;
    --ink-soft: #e6e8f2;
    --emboss: #56608a;
    --rule: rgba(255,255,255,0.85);
  }
  * { box-sizing: border-box; margin: 0; padding: 0; }
  html, body {
    width: 1200px; height: 900px; overflow: hidden;
    background: var(--backdrop);
  }
  .sheet {
    width: 1200px; height: 900px;
    display: flex; flex-direction: column; align-items: center; justify-content: center;
    gap: 40px;
  }
  .card {
    width: 700px; height: 400px;
    background: linear-gradient(160deg, var(--card-navy) 0%, var(--card-navy-deep) 100%);
    position: relative;
  }

  /* Firm name placeholder: plain text with one square */
  .firm {
    display: flex; flex-direction: column; align-items: center; gap: 18px;
    font-family: "Montserrat", sans-serif; font-weight: 500;
  }
  .firm__square { width: 36px; height: 36px; }
  .firm__name { font-size: 30px; line-height: 1; white-space: nowrap; }

  /* Front side */
  .card--front { display: flex; align-items: center; justify-content: center; }
  .card--front .firm { color: var(--emboss); }
  .card--front .firm__square { background: var(--emboss); }

  /* Back side */
  .card--back {
    display: grid; grid-template-columns: 1fr 1px 1fr;
    align-items: center; padding: 0 40px;
  }
  .card--back .firm { color: var(--ink-white); }
  .card--back .firm__square { background: var(--ink-white); }
  .card--back .firm__name { font-size: 28px; }
  .divider { width: 1px; height: 210px; background: var(--rule); }
  .contact {
    padding-left: 40px; color: var(--ink-soft);
    font-family: "Montserrat", sans-serif;
  }
  .contact__name {
    font-family: "Cinzel", serif; font-weight: 600;
    font-size: 24px; color: var(--ink-white); letter-spacing: 0.5px; line-height: 1.1;
  }
  .contact__role { font-size: 15px; margin-top: 2px; }
  .contact__address { font-style: normal; font-size: 16px; line-height: 1.4; margin-top: 14px; }
  .contact__list { list-style: none; margin-top: 14px; font-size: 16px; }
  .contact__list li { display: flex; align-items: center; gap: 12px; line-height: 1.6; }
  .icon { width: 14px; height: 14px; flex: none; }
  .icon * { fill: none; stroke: var(--ink-soft); stroke-width: 1.5; stroke-linecap: round; stroke-linejoin: round; }
</style>
</head>
<body>
<main class="sheet">

  <section class="card card--front" aria-label="Card front">
    <div class="firm">
      <span class="firm__square"></span>
      <span class="firm__name">Quayvale Legal</span>
    </div>
  </section>

  <section class="card card--back" aria-label="Card back">
    <div class="firm">
      <span class="firm__square"></span>
      <span class="firm__name">Quayvale Legal</span>
    </div>

    <span class="divider"></span>

    <div class="contact">
      <h1 class="contact__name">PAUL WHITCOMBE</h1>
      <p class="contact__role">Managing Partner</p>
      <address class="contact__address">Level 9, 7 Ferris Lane<br>Sydney NSW 2000</address>
      <ul class="contact__list">
        <li>
          <svg class="icon" viewBox="0 0 14 14" aria-hidden="true"><path d="M3 1.5l2 2.5-1.2 1.5c.8 1.8 2 3 3.7 3.8L9 8l2.5 2-1.3 2.2C6 12 2 8 1.8 3z"/></svg>
          02 9364 2710
        </li>
        <li>
          <svg class="icon" viewBox="0 0 14 14" aria-hidden="true"><rect x="3.5" y="1" width="7" height="12" rx="1.2"/><path d="M6 10.8h2"/></svg>
          02 8472 3159
        </li>
        <li>
          <svg class="icon" viewBox="0 0 14 14" aria-hidden="true"><rect x="1" y="3" width="12" height="8.5" rx="1"/><path d="M1.5 3.5L7 8l5.5-4.5"/></svg>
          paul@qvlegal.com.au
        </li>
        <li>
          <svg class="icon" viewBox="0 0 14 14" aria-hidden="true"><circle cx="7" cy="7" r="6"/><ellipse cx="7" cy="7" rx="2.6" ry="6"/><path d="M1 7h12M2 4h10M2 10h10"/></svg>
          www.qvlegal.com.au
        </li>
      </ul>
    </div>
  </section>

</main>
</body>
</html>
```